Basic business card

use my newly created logo - and the phrases (Leaner Test Economics & Faster New Silicon Launch Cycles) - and my new email domain / ID - use at conferences / tradeshows

Industry/Entity Type

semiconductor

Contact Information for Business Card

Daniel K Forde, Owner, communicate via Logo - Lower COT - Cost of Test, Accelerated NPI - New Product Introduction, phone +1 555 613 0946, Larkfield, Nevada, USA, daniel.forde@qal-vub.com

Font styles to use
Sans Serif

Requirements
Nice to have
• re-use my logo created via Pixel Harbor last August (#7315926)

```html
<!DOCTYPE html>
<html lang="en">
<head>
<meta charset="utf-8">
<title>QAL-VUB Business Card</title>
<link href="https://fonts.googleapis.com/css2?family=Montserrat:wght@400;500;700&display=swap" rel="stylesheet">
<style>
  :root {
    --backdrop: #cfd3d4;
    --paper: #f7f7f6;
    --navy: #1d2540;
    --ink: #2a2d33;
    --muted: #4a4d54;
    --brand-blue: #1f6fb8;
    --edge-blue: #1a3f9c;
    --divider: #9ea3ab;
    --icon-orange: #e07b12;
    --icon-blue: #2a5fb0;
    --icon-green: #5a9a24;
  }
  * { margin: 0; padding: 0; box-sizing: border-box; }
  html, body {
    width: 1200px; height: 829px; overflow: hidden;
    background: var(--backdrop);
    font-family: "Montserrat", sans-serif;
  }
  .sheet {
    width: 1200px; height: 829px;
    display: flex; align-items: center; justify-content: center; gap: 60px;
  }
  .card {
    position: relative;
    width: 520px; height: 297px;
    background: var(--paper);
    border-bottom: 4px solid var(--edge-blue);
    box-shadow: 0 14px 30px rgba(0,0,0,0.18);
  }
  .wordmark {
    display: flex; align-items: center; gap: 12px;
    color: var(--navy); font-weight: 700; letter-spacing: 0.02em;
    white-space: nowrap;
  }
  .wordmark-mark { background: var(--brand-blue); }

  /* Contact side */
  .card-contact { display: flex; align-items: center; padding: 0 34px; }
  .card-contact .wordmark { font-size: 34px; width: 230px; }
  .card-contact .wordmark-mark { width: 14px; height: 14px; }
  .contact-divider { width: 1px; height: 150px; background: var(--divider); margin: 0 26px 0 4px; flex: none; }
  .contact-block { color: var(--ink); }
  .person-name { font-size: 19px; font-weight: 700; color: var(--navy); white-space: nowrap; }
  .person-role { font-size: 12px; color: var(--muted); margin: 2px 0 16px; }
  .contact-list { list-style: none; font-size: 12.5px; }
  .contact-list li { display: flex; align-items: center; gap: 7px; margin-bottom: 7px; white-space: nowrap; }
  .contact-list svg { width: 12px; height: 12px; flex: none; }

  /* Brand side */
  .card-brand { display: flex; flex-direction: column; align-items: center; justify-content: center; }
  .card-brand .wordmark { font-size: 58px; }
  .card-brand .wordmark-mark { width: 22px; height: 22px; }
  .tagline { margin-top: 22px; font-size: 13.5px; color: var(--brand-blue); letter-spacing: 0.03em; white-space: nowrap; }
</style>
</head>
<body>
<main class="sheet">
  <section class="card card-contact">
    <div class="wordmark"><span class="wordmark-mark"></span>QAL-VUB</div>
    <div class="contact-divider"></div>
    <div class="contact-block">
      <h1 class="person-name">Daniel K Forde</h1>
      <p class="person-role">Owner</p>
      <ul class="contact-list">
        <li>
          <svg viewBox="0 0 12 12" aria-hidden="true"><path d="M2 1h2.5l1 3-1.5 1a6 6 0 0 0 3 3l1-1.5 3 1V10a1 1 0 0 1-1 1A9 9 0 0 1 1 2a1 1 0 0 1 1-1z" fill="var(--icon-orange)"/></svg>
          +1 555 613 0946
        </li>
        <li>
          <svg viewBox="0 0 12 12" aria-hidden="true"><rect x="0.5" y="2" width="11" height="8" fill="var(--icon-blue)"/><path d="M0.5 2l5.5 4.5L11.5 2M0.5 10l4-4M11.5 10l-4-4" stroke="#fff" stroke-width="1" fill="none"/></svg>
          daniel.forde@qal-vub.com
        </li>
        <li>
          <svg viewBox="0 0 12 12" aria-hidden="true"><path d="M6 11.5S2 7 2 4.5a4 4 0 0 1 8 0C10 7 6 11.5 6 11.5z" fill="var(--icon-green)"/><circle cx="6" cy="4.5" r="1.5" fill="#fff"/></svg>
          Larkfield, Nevada, USA
        </li>
      </ul>
    </div>
  </section>

  <section class="card card-brand">
    <div class="wordmark"><span class="wordmark-mark"></span>QAL-VUB</div>
    <p class="tagline">Leaner Test Economics &amp; Faster New Silicon Launch Cycles</p>
  </section>
</main>
</body>
</html>
```